Coastal Learner Bureau business cards

Australian company about to start offering its services. We recruit international students to come to study English, vocational education and postgraduate courses in Australia. We help them find the institution and select the right city they want to come to Australia. We are a young, online oriented and supportive agency. Our clients are between 18 and 35 years old, mainly University students, young professionals or people with work experience. We provide much more information that any other agency offer. We administrate a Facebook group with more than 11.000 members that daily ask questions about general information when coming to Australia, while they are here and even after they leave the country

Target Market(s)

International students from South America, Central America and Europe

Industry/Entity Type

Student

Contact Information for Business Card

Tomas Bilbrea
Managing Director
tomas@kelvarin.com.au
www.kelvoria.com.au
+61 491058264
Melbourne, Australia

Font styles to use
Serif
Sans Serif

Colors

Designer to choose colors to be used in the design.

Requirements
Must have
• Horizontal design
• Standard business card size and shape. If font uses green or yellow colours, they will have to match the ones from the logo
Nice to have
• UPDATE: Use the contents of the green image to design one of the card sides. Use our logo in the background of that side as watermark.
• Passport image, or immigration stamps. A picture of the Yarra River (from Melbourne) would be cool as well.
Should not have
• Non-standard business card size and shape
• Not black as the background colour of any sides as we are not a VIP agency or a hight class service. We are orientes to young people and they like colours, pictures, something attractive.
• Vertical design
• NO YELLOW or BLACK AS THE BACKGROUND COLOUR OF ANY SIDE OF THE BIZ CARD

```html
<!DOCTYPE html>
<html lang="en">
<head>
<meta charset="utf-8">
<title>Coastal Learner Bureau – Business Cards</title>
<link href="https://fonts.googleapis.com/css2?family=Open+Sans:wght@400;600;700&display=swap" rel="stylesheet">
<style>
  :root {
    --page-bg: #3a3b3d;
    --card-white: #f2f2f1;
    --brand-green: #1b6b3e;
    --brand-green-light: #22804a;
    --brand-green-dark: #145a33;
    --brand-gold: #e2bd12;
    --text-white: #ffffff;
  }
  * { box-sizing: border-box; margin: 0; padding: 0; }
  html, body {
    width: 1200px; height: 900px; overflow: hidden;
    background: var(--page-bg);
    font-family: "Open Sans", Arial, sans-serif;
  }
  .stage {
    width: 1200px; height: 900px;
    display: flex; flex-direction: column;
    align-items: center; justify-content: center; gap: 56px;
  }
  .card {
    position: relative;
    width: 600px; height: 343px;
    border-radius: 4px;
    overflow: hidden;
    box-shadow: 0 10px 28px rgba(0,0,0,.45);
  }

  /* Front side */
  .card-front {
    background: linear-gradient(100deg, var(--brand-green-light) 0%, var(--brand-green-dark) 100%);
  }
  .front-brand {
    position: absolute; left: 0; right: 0; top: 122px;
    display: flex; align-items: center; justify-content: center; gap: 12px;
    color: var(--text-white);
  }
  .brand-dot {
    width: 14px; height: 14px; border-radius: 50%;
    background: currentColor;
  }
  .brand-name {
    font-weight: 700; font-size: 46px; letter-spacing: 1px; line-height: 1;
  }
  .tagline-row {
    position: absolute; left: 40px; right: 40px; top: 222px;
    display: flex; align-items: center; gap: 10px;
    color: var(--text-white);
  }
  .tagline-rule { flex: 1; height: 1px; background: var(--brand-gold); }
  .tagline { font-size: 13px; font-weight: 600; white-space: nowrap; }

  /* Back side */
  .card-back { background: var(--card-white); }
  .back-shape { position: absolute; inset: 0; width: 100%; height: 100%; }
  .back-brand {
    position: absolute; left: 58px; top: 150px;
    display: flex; align-items: center; gap: 9px;
    color: var(--brand-green);
  }
  .back-brand .brand-name { font-size: 36px; }
  .back-brand .brand-dot { width: 12px; height: 12px; }
  .contact {
    position: absolute; right: 30px; top: 92px;
    text-align: right; color: var(--text-white);
    font-size: 13px; line-height: 1.55;
  }
  .contact-name { font-weight: 700; font-size: 15px; text-transform: uppercase; letter-spacing: .3px; }
  .contact-role { font-size: 14px; text-transform: uppercase; margin-bottom: 10px; }
  .contact-line { display: flex; justify-content: flex-end; align-items: center; gap: 7px; }
  .contact-line svg { width: 12px; height: 12px; flex: none; }
  .icon-spacer { width: 12px; }
</style>
</head>
<body>
<main class="stage">

  <section class="card card-front" aria-label="Business card front">
    <div class="front-brand">
      <span class="brand-dot"></span>
      <span class="brand-name">Kelvoria</span>
    </div>
    <div class="tagline-row">
      <span class="tagline-rule"></span>
      <span class="tagline">Hacemos más por ti!</span>
      <span class="tagline-rule"></span>
    </div>
  </section>

  <section class="card card-back" aria-label="Business card back">
    <svg class="back-shape" viewBox="0 0 600 343" preserveAspectRatio="none" aria-hidden="true">
      <defs>
        <linearGradient id="greenBand" x1="0" y1="0" x2="1" y2="1">
          <stop offset="0" stop-color="#1f7745"/>
          <stop offset="1" stop-color="#145a33"/>
        </linearGradient>
      </defs>
      <path d="M370,0 C322,160 228,292 28,343 L600,343 L600,0 Z" fill="var(--brand-gold)"/>
      <path d="M376,0 C338,150 264,282 84,343 L600,343 L600,0 Z" fill="url(#greenBand)"/>
    </svg>

    <div class="back-brand">
      <span class="brand-dot"></span>
      <span class="brand-name">Kelvoria</span>
    </div>

    <div class="contact">
      <div class="contact-name">Tomas Bilbrea</div>
      <div class="contact-role">Managing Director</div>
      <div class="contact-line"><span>Melbourne, Australia</span><span class="icon-spacer"></span></div>
      <div class="contact-line">
        <span>+61 491058264</span>
        <svg viewBox="0 0 12 12" aria-hidden="true"><path d="M2.5 1 L4.5 1 L5.2 3.3 L4 4.2 C4.6 5.6 6.2 7.3 7.8 8 L8.7 6.8 L11 7.5 L11 9.5 C11 10.3 10.3 11 9.5 11 C5 11 1 7 1 2.5 C1 1.7 1.7 1 2.5 1 Z" fill="#fff"/></svg>
      </div>
      <div class="contact-line">
        <span>tomas@kelvarin.com.au</span>
        <svg viewBox="0 0 12 12" aria-hidden="true"><rect x="0.5" y="2.5" width="11" height="7.5" rx="1" fill="#fff"/><path d="M1 3 L6 7 L11 3" fill="none" stroke="#145a33" stroke-width="1"/></svg>
      </div>
      <div class="contact-line">
        <span>www.kelvoria.com.au</span>
        <svg viewBox="0 0 12 12" aria-hidden="true"><circle cx="6" cy="6" r="5.5" fill="#fff"/><path d="M0.5 6 H11.5 M6 0.5 C3.5 3.5 3.5 8.5 6 11.5 M6 0.5 C8.5 3.5 8.5 8.5 6 11.5" fill="none" stroke="#145a33" stroke-width=".8"/></svg>
      </div>
    </div>
  </section>

</main>
</body>
</html>
```